Real estate broker business card

Want a modern celan but effective business card for my residential and commercial real estate business. I want the back of the card to advertise my services and to capture business. I have attached the back of my current business card fore ideas
Updates

Logos, photo and text updates added! Added Saturday, September 3, 2016

Project Deadline Extended Reason: LOGOS, PHOTOS AND TEST JUST UPLOADED! I'M READY TO PICK A DESIGN! THANK YOU! Added Saturday, September 3, 2016

Target Market(s)

home buyers and seller. commercial buyers and sellers

Industry/Entity Type

Real Estate

Contact Information for Business Card

must have my contact information and my photo

Requirements
Must have
• Carla Ventrino
• Owner & Qualifying Broker
• Ventrino Real Estate Services
• 505.718.2094
• carla@ventrinohomes.example
• www.ventrinohomes.example
Nice to have
• metallic
• Business capture text: " Don't buy or lease property without someone looking out for your best interests. I will represent you on your home or investment purchase for FREE!"
• "Home owners, call today to receive a FREE market analysis for your homes value!

```html
<!DOCTYPE html>
<html lang="en">
<head>
<meta charset="utf-8">
<title>Ventrino Real Estate Services – Business Card</title>
<link rel="stylesheet" href="https://fonts.googleapis.com/css2?family=Montserrat:wght@400;500;600&family=Playfair+Display:wght@700&display=swap">
<style>
  :root {
    --bg: #3a3a3a;
    --card: #050505;
    --teal: #2a97a6;
    --silver: #c9cdd1;
    --white: #f4f4f4;
    --muted: #d6d6d6;
    --frame: #ffffff;
    --photo-a: #2f4a2c;
    --photo-b: #7a5a4c;
  }
  * { box-sizing: border-box; margin: 0; padding: 0; }
  html, body { width: 1200px; height: 900px; overflow: hidden; }
  body {
    background: var(--bg);
    font-family: "Montserrat", Arial, sans-serif;
    color: var(--white);
    display: flex;
    flex-direction: column;
    align-items: center;
    justify-content: center;
    gap: 36px;
  }
  .card {
    position: relative;
    width: 700px;
    height: 400px;
    background: var(--card);
    border-radius: 22px;
    box-shadow: 0 10px 30px rgba(0,0,0,.45);
    overflow: hidden;
  }

  /* Front */
  .brand {
    position: absolute;
    left: 44px;
    top: 140px;
    width: 350px;
    display: flex;
    align-items: center;
    gap: 14px;
  }
  .brand-mark {
    width: 40px; height: 40px;
    background: var(--teal);
    flex: none;
  }
  .brand-name {
    font-family: "Montserrat", Arial, sans-serif;
    font-weight: 600;
    font-size: 20px;
    line-height: 1.25;
    letter-spacing: .5px;
    color: var(--teal);
    text-transform: uppercase;
  }
  .portrait-frame {
    position: absolute;
    right: 44px;
    top: 34px;
    width: 228px;
    height: 196px;
    border: 4px solid var(--frame);
  }
  .portrait {
    width: 100%; height: 100%;
    background: radial-gradient(ellipse at 55% 60%, var(--photo-b) 0%, #4a3a30 35%, var(--photo-a) 75%);
  }
  .pitch {
    position: absolute;
    left: 44px;
    top: 232px;
    width: 420px;
    font-size: 15.5px;
    line-height: 1.35;
    font-weight: 500;
  }
  .pitch p + p { margin-top: 12px; }

  /* Back */
  .back-brand {
    position: absolute;
    left: 40px;
    top: 0; bottom: 0;
    width: 320px;
    display: flex;
    flex-direction: column;
    align-items: center;
    justify-content: center;
    gap: 18px;
  }
  .back-brand .brand-mark { width: 56px; height: 56px; }
  .back-brand .brand-name { font-size: 22px; text-align: center; line-height: 1.3; }
  .divider {
    position: absolute;
    left: 388px;
    top: 120px;
    width: 1.5px;
    height: 160px;
    background: linear-gradient(var(--card), var(--silver), var(--card));
  }
  .contact {
    position: absolute;
    left: 420px;
    top: 118px;
  }
  .contact-name {
    font-family: "Playfair Display", Georgia, serif;
    font-weight: 700;
    font-size: 26px;
    letter-spacing: .5px;
    text-transform: uppercase;
  }
  .contact-title {
    font-size: 15px;
    color: var(--muted);
    margin: 2px 0 14px;
  }
  .contact-list { list-style: none; }
  .contact-list li {
    display: flex;
    align-items: center;
    gap: 10px;
    font-size: 15px;
    line-height: 1.6;
    color: var(--muted);
  }
  .contact-list svg { width: 13px; height: 13px; fill: var(--muted); flex: none; }
</style>
</head>
<body>

  <section class="card card-front">
    <div class="portrait-frame">
      <div class="portrait" role="img" aria-label="Portrait photo of Carla Ventrino"></div>
    </div>
    <div class="brand">
      <span class="brand-mark"></span>
      <span class="brand-name">Ventrino<br>Real Estate Services</span>
    </div>
    <div class="pitch">
      <p>Don't buy or lease property without someone looking out for your best interests. I will represent you on your home or investment purchase for FREE!</p>
      <p>Home owners, call today to receive a FREE market analysis for your homes value!</p>
    </div>
  </section>

  <section class="card card-back">
    <div class="back-brand">
      <span class="brand-mark"></span>
      <span class="brand-name">Ventrino<br>Real Estate Services</span>
    </div>
    <div class="divider"></div>
    <div class="contact">
      <h1 class="contact-name">Carla Ventrino</h1>
      <p class="contact-title">Owner &amp; Qualifying Broker</p>
      <ul class="contact-list">
        <li>
          <svg viewBox="0 0 24 24" aria-hidden="true"><path d="M6.6 10.8a15.1 15.1 0 0 0 6.6 6.6l2.2-2.2a1 1 0 0 1 1-.25 11.4 11.4 0 0 0 3.6.57 1 1 0 0 1 1 1V20a1 1 0 0 1-1 1A17 17 0 0 1 3 4a1 1 0 0 1 1-1h3.5a1 1 0 0 1 1 1c0 1.250.2 2.450.57 3.57a1 1 0 0 1-.25 1z"/></svg>
          505.718.2094
        </li>
        <li>
          <svg viewBox="0 0 24 24" aria-hidden="true"><path d="M2 5h20v14H2zm2 2v.5l8 5 8-5V7zm0 2.8V17h16V9.8l-8 5z"/></svg>
          carla@ventrinohomes.example
        </li>
        <li>
          <svg viewBox="0 0 24 24" aria-hidden="true"><path d="M12 2a10 10 0 1 0 0 20 10 10 0 0 0 0-20zm6.9 9h-3a15 15 0 0 0-1.3-5.6A8 8 0 0 1 18.9 11zM12 4c.9 1.2 1.8 3.6 1.9 7h-3.8c.1-3.4 1-5.8 1.9-7zM9.4 5.4A15 15 0 0 0 8.1 11h-3a8 8 0 0 1 4.3-5.6zM5.1 13h3a15 15 0 0 0 1.3 5.6A8 8 0 0 1 5.1 13zM12 20c-.9-1.2-1.8-3.6-1.9-7h3.8c-.1 3.4-1 5.8-1.9 7zm2.6-1.4a15 15 0 0 0 1.3-5.6h3a8 8 0 0 1-4.3 5.6z"/></svg>
          www.ventrinohomes.example
        </li>
      </ul>
    </div>
  </section>

</body>
</html>
```